Business Card Design for Training Business

Clear Path Coaching is a new business that delivers training and other services with a focus on topics related to mental health and wellbeing, for example, Wellmind Response Course, Resilience etc. We have a strong focus on evidence-based psychology and neuroscience. I have a logo which I will upload with the brief, so please consider colours that work well with the logo.
Target Market(s)
Adults, workplaces (particularly government and not-for-profits)
Industry/Entity Type
Business
Contact Information for Business Card
Head Strong TrainingSamantha SellwoodDirector0438 770 850sam@headstrongtraining.com.auwww.headstrongtraining.com.au

```html
<!DOCTYPE html>
<html lang="en">
<head>
<meta charset="utf-8">
<title>Clear Path Coaching – Business Card</title>
<link rel="stylesheet" href="https://fonts.googleapis.com/css2?family=Open+Sans:wght@300;400;700&display=swap">
<style>
  :root {
    --page-bg: #e9e7e4;
    --card-white: #ffffff;
    --band-cyan: #5bc3df;
    --band-taupe: #8a7b73;
    --ink: #1c1c1c;
    --brand-grey: #9b9b9b;
    --brand-teal: #7ccfc8;
  }
  * { margin: 0; padding: 0; box-sizing: border-box; }
  html, body {
    width: 1200px; height: 892px; overflow: hidden;
    background: var(--page-bg);
    font-family: "Open Sans", Arial, sans-serif;
  }
  .card {
    position: absolute; left: 150px; top: 189px;
    width: 900px; height: 514px;
    background: var(--card-white);
    box-shadow: 0 10px 30px rgba(0,0,0,0.18);
    overflow: hidden;
  }
  .card-bands { position: absolute; inset: 0; }
  .brand {
    position: absolute; left: 0; right: 0; top: 44px;
    text-align: center;
  }
  .brand-mark {
    display: block; margin: 0 auto 20px;
    width: 100px; height: 100px; border-radius: 50%;
    border: 3px solid var(--brand-teal);
  }
  .brand-name {
    font-weight: 300; font-size: 32px; letter-spacing: 5px;
    color: var(--brand-grey); text-transform: uppercase;
  }
  .person {
    position: absolute; right: 495px; top: 222px;
    text-align: right; color: var(--ink); font-weight: 700;
  }
  .person-name { font-size: 28px; line-height: 1.2; }
  .person-role { font-size: 19px; margin-top: 2px; }
  .divider {
    position: absolute; left: 430px; top: 210px;
    width: 2px; height: 122px; background: var(--ink);
  }
  .contacts {
    position: absolute; left: 448px; top: 222px;
    list-style: none; color: var(--ink); font-size: 21px;
  }
  .contacts li { display: flex; align-items: center; height: 30px; }
  .contact-icon { width: 18px; height: 18px; margin-right: 8px; flex: none; }
</style>
</head>
<body>
  <main class="card">
    <svg class="card-bands" viewBox="0 0 900 514" width="900" height="514" aria-hidden="true">
      <path d="M0 310 C250 410 600 440 900 370 L900 514 L0 514 Z" fill="var(--band-taupe)"/>
      <path d="M0 310 C250 415 520 450 900 505 L900 514 L0 514 Z" fill="var(--band-cyan)"/>
    </svg>

    <header class="brand">
      <span class="brand-mark"></span>
      <div class="brand-name">Clear Path Coaching</div>
    </header>

    <div class="person">
      <div class="person-name">Rebecca Tanfield</div>
      <div class="person-role">Director</div>
    </div>

    <div class="divider"></div>

    <ul class="contacts">
      <li>
        <svg class="contact-icon" viewBox="0 0 18 18" aria-hidden="true"><rect width="18" height="18" rx="2" fill="var(--ink)"/><path d="M5 3.5 L7.5 3.5 L8.5 6.5 L7 7.8 C7.8 9.6 8.6 10.4 10.2 11 L11.5 9.5 L14.5 10.5 L14.5 13 C9 14 4 9 5 3.5 Z" fill="#fff"/></svg>
        0491 362 517
      </li>
      <li>
        <svg class="contact-icon" viewBox="0 0 18 18" aria-hidden="true"><rect width="18" height="18" rx="2" fill="var(--ink)"/><rect x="3" y="5" width="12" height="8" fill="#fff"/><path d="M3 5 L9 10 L15 5" stroke="var(--ink)" stroke-width="1.2" fill="none"/></svg>
        bec@clearpathcoaching.example.au
      </li>
      <li>
        <svg class="contact-icon" viewBox="0 0 18 18" aria-hidden="true"><rect width="18" height="18" rx="2" fill="var(--ink)"/><circle cx="9" cy="9" r="5.5" stroke="#fff" stroke-width="1.4" fill="none"/><path d="M3.5 9 H14.5 M9 3.5 C6.5 6 6.5 12 9 14.5 M9 3.5 C11.5 6 11.5 12 9 14.5" stroke="#fff" stroke-width="1" fill="none"/></svg>
        www.clearpathcoaching.example.au
      </li>
    </ul>
  </main>
</body>
</html>
```